UI and Graphic Design for Web-based Software

Webpage design: to refine website UI and graphic design based on wireframes to be provided by us. Scope of work is 4-5 pages which all have the same look/feel and basic structure. Also required are related interface icons and badges, and the main banner on the home page.

Industry/Entity Type

Graphic Design

Requirements
Must have
• Some design elements will require additional time and revision rounds: homepage banner, interface icons, badges.

```html
<!DOCTYPE html>
<html lang="en">
<head>
<meta charset="utf-8">
<title>Chatter Desk</title>
<link rel="stylesheet" href="https://fonts.googleapis.com/css2?family=Arimo:wght@400;700&family=Archivo+Black&family=Open+Sans:wght@400&display=swap">
<style>
:root{
  --red:#f0084a;
  --red-soft:#f5507c;
  --dark:#2d2d2d;
  --panel:#f2f2f3;
  --line:#d9d9dc;
  --pink-row:#fde4eb;
  --pink-line:#f7b6c8;
  --text:#222;
  --blue:#1e9ee6;
  --btn-a:#3d5c9a;
  --btn-b:#8fd1ef;
}
*{box-sizing:border-box;margin:0;padding:0}
html,body{width:1200px;height:900px;overflow:hidden;background:#fff}
body{position:relative;font-family:Arimo,Arial,sans-serif;color:var(--text);font-size:12px}
.abs{position:absolute}

.topbar{left:163px;top:0;width:876px;height:48px;background:var(--dark)}
.brand-mark{left:0;top:0;width:68px;height:48px;background:var(--red)}
.brand-name{left:90px;top:8px;color:#fff;font-size:21px;font-weight:700}
.brand-sub{left:90px;top:29px;color:#fff;font-size:10px}
.lang{left:796px;top:14px;width:65px;height:20px;background:#fff;font-size:10px;padding:4px 5px;border-radius:2px}
.lang::after{content:"";position:absolute;right:6px;top:8px;border:3px solid transparent;border-top-color:#333}

.banner{left:163px;top:61px;width:675px;height:162px;background:var(--dark);color:#fff}
.banner h1{position:absolute;left:11px;top:16px;font-family:"Archivo Black",Arial,sans-serif;font-size:41px;line-height:32px;letter-spacing:-2.5px;font-weight:400}
.feature{position:absolute;left:426px;display:flex;align-items:center;gap:12px;font-family:"Open Sans",Arial,sans-serif;font-size:18px;line-height:20px}
.feature svg{width:28px;height:28px;flex:none}

.auth{left:847px;top:61px;width:192px;height:224px;background:var(--panel);border:1px solid var(--line)}
.btn-red{position:absolute;height:26px;background:var(--red);color:#fff;font-size:12px;text-align:center;line-height:26px;border-radius:2px}
.auth label{position:absolute;left:9px;font-size:9px}
.auth .field{position:absolute;left:9px;width:171px;height:28px;background:#fff;border:1px solid var(--line)}
.remember{left:9px;top:155px;color:#bbb;font-size:11px;display:flex;gap:6px;align-items:center}
.remember i{width:10px;height:10px;border:1px solid #ccc;background:#fff}
.net-btn{position:absolute;top:194px;height:21px;color:#fff;font-size:10px;font-weight:700;display:flex;align-items:center;gap:5px;padding-left:5px;border-radius:2px}
.net-btn i{width:11px;height:11px;background:rgba(255,255,255,.85)}

.search{left:163px;top:240px;width:675px;height:45px;background:var(--panel);border:1px solid var(--line)}
.search .input{position:absolute;left:9px;top:9px;width:576px;height:27px;background:#fff;border:1px solid var(--line);font-size:13px;padding:6px 10px}
.search .go{position:absolute;left:603px;top:10px;width:61px;height:24px;background:var(--red);border-radius:2px}

.results{left:163px;top:304px;width:675px;height:35px;background:var(--panel);border:1px solid var(--line);color:var(--red);font-size:16px;padding:8px 16px}

.cats{left:163px;top:356px;width:190px}
.cats h2{font-size:15px;color:var(--red);font-weight:400;padding-left:2px;margin-bottom:6px}
.cats li{list-style:none;font-size:13px;height:27px;line-height:27px;padding-left:20px;position:relative}
.cats li.active{color:var(--red)}
.cats li.active::before{content:"";position:absolute;left:0;top:2px;width:4px;height:26px;background:var(--red)}
.cats li.sub{padding-left:48px;height:21.5px;line-height:21.5px}

.thread{left:363px;top:349px;width:475px;height:366px}
.thread > *{position:absolute;left:0;width:475px}
.row{height:27px;font-size:11px;line-height:27px;padding-left:9px}
.row.lined{border-bottom:1px solid var(--pink-line)}
.row .meta{position:absolute;left:218px;font-style:italic}
.row .time{position:absolute;left:337px;font-weight:700}
.src{position:absolute;left:405px;top:7px;width:14px;height:14px;background:#4d6aa6}
.src.chirp{background:#55b6e6}
.flag{position:absolute;left:430px;top:5px;width:27px;height:17px;background:#e0201b}
.reply{font-size:11px;line-height:13px}
.reply.lined{border-bottom:1px solid var(--pink-line)}
.reply p{position:absolute;left:53px;width:345px}
.avatar{position:absolute;left:9px;width:39px;height:36px}
.reply u{text-decoration:underline}
.more{height:14px}
.more::before,.more::after{content:"";position:absolute;left:0;right:0;height:1px;background:var(--pink-line)}
.more::before{top:3px}.more::after{top:9px}
.more span{position:absolute;left:200px;top:0;z-index:1;background:var(--red);color:#fff;font-size:9px;line-height:12px;padding:0 8px;border-radius:2px}

.influencers{left:850px;top:304px;width:189px}
.influencers h2{height:35px;background:var(--red);color:#fff;font-size:17px;font-weight:400;padding:8px 10px}
.inf{height:27px;display:flex;align-items:center;font-size:11px;color:#555;padding:0 6px}
.inf:nth-child(odd){background:var(--pink-row)}
.inf:nth-child(even){background:#fff2f5}
.inf .n{width:18px;height:18px;background:var(--red);color:#fff;text-align:center;line-height:18px;font-size:11px;margin-right:9px}
.inf .v{margin-left:auto;font-size:12px;color:#444}
.inf-list{margin-top:9px}

.footer{left:163px;top:779px;width:879px;height:90px;background:#ececec}
.map{left:14px;top:14px;width:75px;height:63px;background:linear-gradient(135deg,#e6e2d8,#c9d3c4);border:1px solid #bbb}
.contact-title{left:100px;top:19px;color:var(--blue);font-size:22px}
.contact-line{left:100px;top:55px;font-size:11px}
.follow{left:663px;top:21px;color:#999;font-size:12px;font-weight:700}
.social{left:665px;top:43px;display:flex;gap:10px}
.social i{width:25px;height:25px;background:#ddd;border:1px solid #d0d0d0}

.bottombar{left:163px;top:869px;width:876px;height:31px;background:var(--red);color:#fff;font-size:11px}
.copy{left:11px;top:10px}
.nav{right:0;top:0;display:flex;height:31px}
.nav a{color:#fff;text-decoration:none;line-height:31px;padding:0 8px}
.nav a.on{background:var(--red-soft);padding:0 11px}
</style>
</head>
<body>

<header class="abs topbar">
  <div class="abs brand-mark"></div>
  <div class="abs brand-name">Chatter Desk</div>
  <div class="abs brand-sub">Powerd By Emberline</div>
  <div class="abs lang">English</div>
</header>

<section class="abs banner">
  <h1>The Search &amp;<br>Authoring Tool for<br>Social Media<br>Everywhere</h1>
  <div class="feature" style="top:11px">
    <svg viewBox="0 0 28 28" fill="none" stroke="#fff" stroke-width="3"><path d="M6 16a8 8 0 0 1 13-9"/><path d="M22 12a8 8 0 0 1-13 9"/><path d="M17 4l3 3-3 3M11 24l-3-3 3-3" stroke-width="2.5"/></svg>
    <span>Find conversations that<br>matter to you</span>
  </div>
  <div class="feature" style="top:64px">
    <svg viewBox="0 0 28 28"><path d="M2 3h24v16H12l-5 6v-6H2z" fill="#fff"/></svg>
    <span>Join any conversation<br>on the internet</span>
  </div>
  <div class="feature" style="top:111px">
    <svg viewBox="0 0 28 28" fill="none" stroke="#fff" stroke-width="2.5"><path d="M3 4v21h23"/><path d="M6 21l7-8 4 4 7-9"/><path d="M19 8h5v5"/></svg>
    <span>Track your influence<br>and get rewarded</span>
  </div>
</section>

<aside class="abs auth">
  <div class="btn-red" style="left:9px;top:8px;width:72px">LOGIN</div>
  <div class="abs" style="left:89px;top:16px;font-size:11px;color:#555">or</div>
  <div class="btn-red" style="left:107px;top:8px;width:73px">SIGNUP</div>
  <label style="top:52px">Email</label>
  <div class="field" style="top:65px"></div>
  <label style="top:103px">Password</label>
  <div class="field" style="top:116px"></div>
  <div class="abs remember"><i></i>Remember Me</div>
  <div class="abs" style="left:10px;top:176px;font-size:9px">Login With :</div>
  <div class="net-btn" style="left:11px;width:77px;background:var(--btn-a)"><i></i>Linkspace</div>
  <div class="net-btn" style="left:105px;width:72px;background:var(--btn-b);color:#2b6f91"><i></i>Chirper</div>
</aside>

<div class="abs search">
  <div class="input">Find Conversations About....</div>
  <div class="go"><svg width="61" height="24" viewBox="0 0 61 24"><circle cx="29" cy="10" r="4" fill="none" stroke="#fff" stroke-width="2"/><path d="M32 13l4 4" stroke="#fff" stroke-width="2.5"/></svg></div>
</div>

<div class="abs results">Results: Showing 453 Conversations on 215 sites, viewed 14,3634 times</div>

<nav class="abs cats">
  <h2>Top Searches by Category</h2>
  <ul>
    <li>Beauty</li>
    <li class="active">Cars and Trucks</li>
    <li class="sub">Classic</li>
    <li class="sub">Electric</li>
    <li class="sub">Exotic</li>
    <li class="sub">Trucks</li>
    <li style="margin-top:4px">Cooking</li>
    <li>Fashion</li>
    <li>Gardening</li>
    <li>Hair care</li>
    <li>Motorcycles</li>
    <li>Restaurants and Bars</li>
    <li>Sports</li>
    <li>Travel</li>
  </ul>
</nav>

<main class="abs thread">
  <div class="row lined" style="top:0;height:28px"><b>Anti-scar cream problame</b> - I tried dermio...<i>(show 4 Responsea)</i><span class="time">10:30 am</span><span class="src"></span><span class="flag"></span></div>
  <div class="row" style="top:28px"><b>Burned my hand</b><span class="meta">(hide 11 Responsea)</span><span class="time">Yesterday</span><span class="src"></span><span class="flag"></span></div>

  <div class="reply lined" style="top:55px;height:54px">
    <div class="avatar" role="img" aria-label="User avatar photo" style="top:6px;background:linear-gradient(135deg,#2f3a48,#7a8696)"></div>
    <p style="top:5px">When I was cooking yesterday, I splled hot oil over my heands, I had a doctor look at It and give me bandages, but &nbsp;now I don't know if if safe for me to tack painkillers ?</p>
  </div>

  <div class="reply" style="top:110px;height:50px">
    <div class="avatar" role="img" aria-label="User avatar photo" style="top:7px;background:linear-gradient(135deg,#5a4638,#c9b9ad)"></div>
    <p style="top:12px">I'm not a doctor, but i did a search on the internet and it looks like painkillers can....</p>
  </div>

  <div class="more" style="top:161px"><span>3 More</span></div>

  <div class="reply lined" style="top:176px;height:54px">
    <div class="avatar" role="img" aria-label="User avatar image" style="top:9px;background:linear-gradient(135deg,#e8eef3,#c7b7c2)"></div>
    <p style="top:22px">You should put some Softbalm on your hands!</p>
  </div>

  <div class="reply lined" style="top:230px;height:54px">
    <svg class="avatar" style="top:10px" viewBox="0 0 39 36" aria-hidden="true"><circle cx="20" cy="12" r="6" fill="#f6b7c8"/><path d="M10 30c0-8 20-8 20 0z" fill="#f6b7c8"/></svg>
    <p style="top:13px;width:290px">Click here to <u>respond</u> to this thread (we will trancelate into Chinese for You), or you can <u>respond direct in chinese</u></p>
  </div>

  <div class="row lined" style="top:284px"><b>About wrinkles</b> - I'm 45 years old and...<i>(show 2 Responsea)</i><span class="src chirp"></span><span class="flag"></span></div>
  <div class="row lined" style="top:311px"><b>About wrinkles</b> - I'm 45 years old and...<i>(show 2 Responsea)</i><span class="src chirp"></span><span class="flag"></span></div>
  <div class="row lined" style="top:338px"><b>About wrinkles</b> - I'm 45 years old and...<i>(show 2 Responsea)</i><span class="src chirp"></span><span class="flag"></span></div>
</main>

<aside class="abs influencers">
  <h2>Top Influencers</h2>
  <div class="inf-list">
    <div class="inf"><span class="n">1</span>比西迪伊<span class="v">17,182,766</span></div>
    <div class="inf"><span class="n">2</span>比西迪伊<span class="v">16,182,766</span></div>
    <div class="inf"><span class="n">3</span>比西迪伊<span class="v">16,000,000</span></div>
    <div class="inf"><span class="n">4</span>比西迪伊<span class="v">15,202,358</span></div>
    <div class="inf"><span class="n">5</span>比西迪伊<span class="v">15,120,807</span></div>
    <div class="inf"><span class="n">6</span>比西迪伊<span class="v">14,120,807</span></div>
    <div class="inf"><span class="n">7</span>比西迪伊<span class="v">13,120,807</span></div>
    <div class="inf"><span class="n">8</span>比西迪伊<span class="v">17,182,766</span></div>
    <div class="inf"><span class="n">9</span>比西迪伊<span class="v">16,182,766</span></div>
    <div class="inf"><span class="n">10</span>比西迪伊<span class="v">16,000,000</span></div>
    <div class="inf"><span class="n">1</span>比西迪伊<span class="v">15,202,358</span></div>
    <div class="inf"><span class="n">2</span>比西迪伊<span class="v">15,120,807</span></div>
    <div class="inf"><span class="n">3</span>比西迪伊<span class="v">14,120,807</span></div>
    <div class="inf"><span class="n">4</span>比西迪伊<span class="v">13,120,807</span></div>
    <div class="inf"><span class="n">5</span>比西迪伊<span class="v">16,000,000</span></div>
  </div>
</aside>

<footer class="abs footer">
  <div class="abs map" role="img" aria-label="Street map showing the office location"></div>
  <div class="abs contact-title">Contact Us</div>
  <div class="abs contact-line">(+86) 400 555 0142, info@emberline.example, Linden Road #42 Room 300-302 Shanghai, China 200000</div>
  <div class="abs follow">Follow Us On :</div>
  <div class="abs social"><i></i><i></i><i></i><i></i><i></i><i></i></div>
</footer>

<div class="abs bottombar">
  <div class="abs copy">Copyright © 2012 Emberline. All Rights Reserved</div>
  <nav class="abs nav">
    <a class="on" href="#">HOME</a><a href="#">ABOUT US</a><a href="#">BLOG</a><a href="#">FAQS</a><a href="#">CONTACT US</a><a href="#">LOGIN</a><a href="#">SIGNUP</a>
  </nav>
</div>

</body>
</html>
```